Counseling Practice Business Card

I need a professional looking business card incorporating my new logo that was just completed. Card needs to incorporate my name and title, description of my specialty, my address, my phone number, my fax number, my email and my website URL. I need to be able to choose design on/with different paper colors and textures.
I do not have a lot of business card ideas so I am open to anything but I want bold,sharp, clear card without additional designs other than my logo (see attached file info). I am open to different color backgrounds or paper colors including black. I do not like traditional brackets around area codes in phone number or dashes between numbers in phone number. Am open to other ways of presenting including periods between numbers as appropriate. I do not know enough to know what I like yet but I want card to coordinate and work together with my logo. My practice emphasizes natural mental health interventions so any use of color (with background paper color or the blue and green in my logo) that elicits nature is nice. In addition to black, any natural brown or wood looking background might be desirable also. Most of the offerings so far look very similar and boring.

Target Market(s)

Potential therapy clients and other professionals

Contact Information for Business Card

Card information:
Gerald M. Whitcombe, Ph.D.
Licensed Clinical Psychologist
Integrative Health Coach
4812 Marlowe Ridge Blvd SE
Suite 310
Duluth, GA 30096
(770) 415-2983 phone
(770) 581-4096 fax
drgeraldwhitcombe@quillmarsh.net
brightfernwellness.net

Font styles to use
Serif
Sans Serif
Other font styles liked:
• anything that you think looks crisp, clear and easily readable

Requirements
Must have
• Any color used should coordinate with my logo design (see attached files).
• Card should be printed horizontally so top and bottom are longest sides of rectangle.
• Background color or paper color should complement and highlight logo. Do not like a white background. black, grey, brown or any color my logo would blend well with.
Nice to have
• I would like designer to utilize color to highlight letters/name or phone-fax-web symbols.
• Bottom edge of card could be highlighted if appropriate to an idea.
Should not have
• I would NOT want the card to have a pure white background at all.
• No clear cards.
• Cards should be oriented with long sides on bottom and top, NOT sides. DO NOT LIKE THIS THIN TALL ORIENTATION.

```html
<!DOCTYPE html>
<html lang="en">
<head>
<meta charset="utf-8">
<title>Brightfern Wellness – Business Card</title>
<link rel="stylesheet" href="https://fonts.googleapis.com/css2?family=Arimo:wght@400;700&display=swap">
<style>
  :root {
    --stage: #2b2b2b;
    --card: #e6e3da;
    --brand-blue: #1f5fa6;
    --name-green: #1b6b2e;
    --ink: #1a1a1a;
    --icon: #1f5fa6;
  }
  * { box-sizing: border-box; margin: 0; padding: 0; }
  html, body {
    width: 1200px; height: 997px; overflow: hidden;
    background: var(--stage);
    font-family: "Arimo", Arial, sans-serif;
  }
  .card {
    position: absolute;
    left: 180px; top: 258px;
    width: 840px; height: 480px;
    background: var(--card);
    box-shadow: 0 18px 40px rgba(0,0,0,.55);
  }
  .brand {
    position: absolute; left: 56px; top: 58px;
    display: flex; align-items: center; gap: 14px;
  }
  .brand-dot {
    width: 26px; height: 26px; border-radius: 50%;
    background: var(--brand-blue);
  }
  .brand-name {
    font-size: 40px; font-weight: 700; color: var(--brand-blue);
    letter-spacing: .5px;
  }
  .identity { position: absolute; left: 56px; top: 210px; }
  .person-name {
    font-size: 27px; font-weight: 700; color: var(--name-green);
    letter-spacing: 1px; text-transform: uppercase;
  }
  .person-name .credential {
    font-weight: 400; text-transform: none; color: var(--brand-blue);
    font-size: 23px; letter-spacing: 0;
  }
  .person-title {
    margin-top: 6px; font-size: 22px; color: var(--brand-blue);
  }
  .address {
    position: absolute; right: 56px; top: 300px;
    font-size: 18px; line-height: 1.5; color: var(--name-green);
    font-style: normal; text-align: left;
  }
  .contact-list {
    position: absolute; left: 56px; bottom: 50px;
    list-style: none; font-size: 21px; color: var(--ink);
    line-height: 1.4;
  }
  .contact-list li { display: flex; align-items: center; gap: 12px; }
  .contact-list svg { width: 16px; height: 16px; flex: none; fill: var(--icon); }
  .contact-list .web { color: var(--brand-blue); font-weight: 700; }
  .sr-label {
    position: absolute; width: 1px; height: 1px; overflow: hidden;
    clip: rect(0 0 0 0); white-space: nowrap;
  }
</style>
</head>
<body>
  <section class="card">
    <div class="brand">
      <span class="brand-dot"></span>
      <span class="brand-name">Brightfern Wellness</span>
    </div>

    <div class="identity">
      <p class="person-name">Gerald M. Whitcombe <span class="credential">Ph.D.</span></p>
      <p class="person-title">Licensed Clinical Psychologist/ Integrative Health Coach</p>
    </div>

    <address class="address">
      4812 Marlowe Ridge Blvd SE<br>
      Suite 310, Duluth, GA 30096
    </address>

    <ul class="contact-list">
      <li class="phone">
        <svg viewBox="0 0 16 16" role="img" aria-label="Phone"><path d="M2 6c0-2 2-3 6-3s6 1 6 3l-3 1-1-2H6L5 7 2 6zm2 2h8l1 6H3l1-6z"/></svg>
        <span class="sr-label">Phone:</span>770.415.2983
      </li>
      <li class="fax">
        <svg viewBox="0 0 16 16" role="img" aria-label="Fax"><path d="M4 1h8v4H4V1zM1 6h14v6h-3v3H4v-3H1V6zm4 4v4h6v-4H5zm7-3v1.5h1.5V7H12z"/></svg>
        <span class="sr-label">Fax:</span>770.581.4096
      </li>
      <li class="email">
        <svg viewBox="0 0 16 16" role="img" aria-label="Email"><path d="M1 3h14v10H1V3zm1.5 1.5L8 9l5.5-4.5v-.5h-11v.5z"/></svg>
        drgeraldwhitcombe@quillmarsh.net
      </li>
      <li class="web">
        <svg viewBox="0 0 16 16" role="img" aria-label="Website"><circle cx="8" cy="8" r="6"/></svg>
        brightfernwellness.net
      </li>
    </ul>
  </section>
</body>
</html>
```